Children’s entertainer/balloon artist Website Home Page and custom landing page

I need a home page design for the home page of a children and family entertainer/balloon twister’s website. I also need a custom landing page for family theatre shows performed by the same entertainer.
It will be a Wordpress website and I need the final artwork in a layer Photoshop file with all the layers clearly named and labeled.

Target Market(s)

The site visitors are mainly mums, aged between early 20’s and late 30’s. Other visitors will included companies for Christmas functions, and event organisers for corporate functions.

Industry/Entity Type

Entertainment

Number of Pages Required

2 page

Font styles to use
Sans Serif

Colors
34a6d7
f37122

Requirements
Must have
• Layout
• I have included a wireframe for the home page layout and the custom landing page for your reference. This is a guide only and I welcome your interpretation with the rough layout provided.
• This website needs to look good on all devices as it will be fully responsive.
• It needs to include a footer area on the page, that has social media and a call to action area included.
• Colours
• The main colours for the site is:
• orange (call to action colour)
• ff6800
• blue/turquoise
• 42abc3
• Pictures
• I have included images of the entertainer/balloon artist for you to use/take inspiration from.
• These images will be included on the website. I want to show lots of people having fun.
• I would like to have elements of the logo used in isolation across the website
• i.e. the octopus figure to be included in the footer or the bird element to be included in the testimonial slider etc.
• Elements to include
• Note: use the images of the entertainer in the boxes on the home page (balloon shows, balloon twisting, balloon workshops, theatre shows (the three little balloon pigs on his head)
Nice to have
Should not have
• Element to avoid
• Stock imagery of balloon sculptures - use images provided.

```html
<!DOCTYPE html>
<html lang="en">
<head>
<meta charset="utf-8">
<title>Benny The Jester – Children's Entertainer</title>
<link rel="stylesheet" href="https://fonts.googleapis.com/css2?family=Fredoka+One&family=Open+Sans:ital,wght@0,400;0,600;0,700;1,400&display=swap">
<style>
:root{
  --blue:#34a6d7;
  --blue-deep:#1d5fa8;
  --blue-dark:#163f78;
  --orange:#f37122;
  --ink:#333a42;
  --muted:#7a8088;
  --light:#f1f2f4;
  --line:#dfe2e6;
  --dark:#22262b;
  --white:#ffffff;
}
*{box-sizing:border-box;margin:0;padding:0}
html,body{width:820px;height:1200px;overflow:hidden}
body{font-family:"Open Sans",Arial,sans-serif;color:var(--ink);background:var(--white);font-size:12px}
.display{font-family:"Fredoka One","Open Sans",sans-serif;font-weight:400}

/* header + hero */
.hero{position:relative;height:440px;background:linear-gradient(135deg,var(--blue-dark) 0%,var(--blue-deep) 45%,var(--blue) 100%);overflow:hidden}
.hero-photo{position:absolute;right:0;top:0;width:520px;height:440px;background:radial-gradient(circle at 55% 55%,#4ba8d9 0%,#2a79bd 45%,rgba(29,95,168,0) 75%)}
.site-header{position:absolute;top:0;left:0;right:0;height:62px;display:flex;align-items:center;justify-content:space-between;padding:0 40px;background:rgba(12,36,72,.35)}
.brand{display:flex;align-items:center;gap:10px;margin-top:34px}
.brand-dot{width:44px;height:44px;border-radius:50%;background:var(--orange)}
.brand-name{font-family:"Fredoka One","Open Sans",sans-serif;font-size:30px;color:var(--white);line-height:1}
.main-nav{display:flex;gap:6px}
.main-nav a{font-size:10px;font-weight:700;letter-spacing:.5px;color:var(--white);text-decoration:none;text-transform:uppercase;padding:6px 10px;border:1px solid rgba(255,255,255,.45);border-radius:14px}
.hero-copy{position:absolute;left:110px;top:175px}
.hero-name{font-size:54px;color:var(--white);line-height:1}
.hero-role{font-size:26px;color:var(--orange);margin-top:4px}
.hero-line{font-size:22px;color:var(--white);line-height:1.25;margin-top:8px}
.btn{display:inline-block;background:var(--orange);color:var(--white);text-decoration:none;font-weight:700;border-radius:3px}
.hero-btn{font-family:"Fredoka One","Open Sans",sans-serif;font-size:17px;padding:9px 18px;margin-top:16px}
.slide-arrow{position:absolute;top:205px}
.slide-arrow.prev{left:30px}
.slide-arrow.next{right:30px}

/* testimonials */
.testimonials{height:230px;display:flex;padding:28px 40px 0 40px;gap:30px}
.testimonial-area{flex:1}
.section-title{font-size:24px;color:var(--ink);text-transform:uppercase}
.section-title span{color:var(--orange)}
.title-rule{height:1px;background:var(--line);margin:10px 0 18px}
.quote{display:flex;gap:18px;align-items:flex-start}
.avatar{width:92px;height:92px;border-radius:50%;background:linear-gradient(135deg,#f4c9a6,#d98e62);flex:none;border:4px solid var(--light)}
.quote-mark{font-family:Georgia,serif;font-size:54px;color:var(--line);line-height:.8}
.quote-name{font-size:11px;font-weight:700;color:var(--blue);text-transform:uppercase}
.quote-role{font-size:9px;color:var(--muted);margin-bottom:6px}
.quote-text{font-size:11px;font-style:italic;color:var(--muted);line-height:1.6;max-width:370px}
.slider-dots{display:flex;justify-content:flex-end;gap:6px;margin-top:6px}
.slider-dots span{width:16px;height:16px;border:1px solid var(--line);border-radius:50%}
.contact-card{width:205px;height:190px;background:var(--dark);border-radius:6px;position:relative;padding:18px 16px;color:var(--white);overflow:hidden}
.contact-title{font-size:11px;font-weight:700;text-transform:uppercase;line-height:1.4}
.contact-call{font-size:11px;margin-top:22px;color:#c7ccd2}
.contact-phone{display:flex;align-items:center;gap:6px;font-weight:700;font-size:13px;margin-top:4px}
.contact-btn{font-size:9px;padding:6px 10px;margin-top:14px;background:var(--blue)}
.contact-photo{position:absolute;right:-6px;top:8px;width:78px;height:182px;background:linear-gradient(180deg,#4aa8dc,#f07e3a 60%,#e25b2c);border-radius:40px 40px 0 0}

/* about + newsletter */
.about{height:230px;background:var(--light);display:flex;padding:26px 40px 0 40px;gap:34px}
.about-body{flex:1}
.about-sub{font-size:12px;font-style:italic;font-weight:600;color:var(--ink);line-height:1.5}
.about-text{font-size:10px;color:var(--muted);line-height:1.6;margin-top:8px}
.small-btn{font-size:9px;padding:6px 12px;margin-top:14px;background:var(--blue)}
.newsletter{width:250px}
.newsletter-text{font-size:9px;color:var(--muted);line-height:1.5;margin-bottom:10px}
.field{height:24px;background:var(--white);border:1px solid var(--line);font-size:9px;color:var(--muted);padding:5px 8px;margin-bottom:8px}

/* service boxes */
.services{height:220px;background:linear-gradient(180deg,#e8eaed 0%,#d4d8dd 100%);display:flex;gap:20px;padding:28px 62px 0}
.service{flex:1;height:170px;border-radius:4px;position:relative;overflow:hidden;background:linear-gradient(160deg,var(--blue) 0%,var(--blue-deep) 70%,var(--blue-dark) 100%)}
.service-photo{position:absolute;left:0;right:0;bottom:0;height:110px;background:radial-gradient(circle at 50% 80%,#f29a5a 0%,rgba(52,166,215,0) 70%)}
.service-title{position:relative;font-size:22px;line-height:1;color:var(--white);text-align:center;padding-top:16px}
.service-btn{position:absolute;left:50%;transform:translateX(-50%);bottom:18px;font-size:8px;padding:5px 10px;text-transform:uppercase}

/* footer */
.site-footer{height:80px;background:var(--dark);padding:14px 40px 0;color:#aab0b8}
.footer-top{display:flex;justify-content:space-between;align-items:center}
.footer-nav{display:flex;gap:16px}
.footer-nav a{font-size:9px;font-weight:700;color:var(--white);text-decoration:none;text-transform:uppercase}
.social{display:flex;gap:6px}
.social span{width:20px;height:20px;border-radius:50%;background:var(--blue)}
.copyright{font-size:9px;margin-top:14px;border-top:1px solid #3a4048;padding-top:10px}
</style>
</head>
<body>

<section class="hero">
  <div class="hero-photo" role="img" aria-label="Photo of Benny the entertainer surrounded by colourful balloon sculptures"></div>
  <header class="site-header">
    <div class="brand"><span class="brand-dot"></span><span class="brand-name">Benny The Jester</span></div>
    <nav class="main-nav">
      <a href="#">Balloon Shows</a><a href="#">Balloon Twisting</a><a href="#">Theatre</a><a href="#">Booking</a><a href="#">Contact Us</a>
    </nav>
  </header>
  <svg class="slide-arrow prev" width="22" height="40" viewBox="0 0 22 40"><path d="M18 3 4 20l14 17" fill="none" stroke="#fff" stroke-width="3"/></svg>
  <svg class="slide-arrow next" width="22" height="40" viewBox="0 0 22 40"><path d="M4 3l14 17L4 37" fill="none" stroke="#fff" stroke-width="3"/></svg>
  <div class="hero-copy">
    <div class="hero-name display">Benny</div>
    <div class="hero-role display">The Entertainer.</div>
    <div class="hero-line display">Will make you laugh<br>like never before!</div>
    <a class="btn hero-btn" href="#">Know More About Me ›</a>
  </div>
</section>

<section class="testimonials">
  <div class="testimonial-area">
    <h2 class="section-title display">Client <span>Testimonials</span></h2>
    <div class="title-rule"></div>
    <div class="quote">
      <div class="avatar" role="img" aria-label="Portrait of a happy parent"></div>
      <div class="quote-mark">“</div>
      <div>
        <div class="quote-name">Rosie Palmer</div>
        <div class="quote-role">Happy Parent</div>
        <p class="quote-text">Benny was brilliant with the kids and kept everyone laughing from start to finish. The balloon animals were a huge hit and every child went home with a smile. We will definitely book him again!</p>
      </div>
    </div>
    <div class="slider-dots"><span></span><span></span></div>
  </div>
  <aside class="contact-card">
    <div class="contact-title">Contact the<br>Entertainer</div>
    <div class="contact-call">Make A Call</div>
    <div class="contact-phone">
      <svg width="12" height="12" viewBox="0 0 24 24"><path d="M6.6 10.8a15 15 0 0 0 6.6 6.6l2.2-2.2a1 1 0 0 1 1-.25 11.4 11.4 0 0 0 3.6.57 1 1 0 0 1 1 1V20a1 1 0 0 1-1 1A17 17 0 0 1 3 4a1 1 0 0 1 1-1h3.5a1 1 0 0 1 1 1c0 1.25.2 2.45.57 3.57a1 1 0 0 1-.25 1z" fill="#f37122"/></svg>
      (020) 555-0148
    </div>
    <a class="btn contact-btn" href="#">Request a Callback</a>
    <div class="contact-photo" role="img" aria-label="Entertainer wrapped in long balloons"></div>
  </aside>
</section>

<section class="about">
  <div class="about-body">
    <h2 class="section-title display">About <span>Benny The Jester</span></h2>
    <div class="title-rule"></div>
    <p class="about-sub">A Kids Entertainer And Balloon Artist Living And Working The South Of The UK, Called Benny</p>
    <p class="about-text">From birthday parties to school fairs and company Christmas functions, Benny brings fun, balloons and laughter to every event. Each show is packed with comedy, magic and crazy balloon creations that children and grown-ups love.</p>
    <a class="btn small-btn" href="#">Read More ›</a>
  </div>
  <div class="newsletter">
    <h2 class="section-title display">Newsletter <span>Sign Up</span></h2>
    <div class="title-rule"></div>
    <p class="newsletter-text">Sign up to our newsletter to get all the latest updates and news from Benny!</p>
    <div class="field">Name</div>
    <div class="field">Email Address</div>
    <a class="btn small-btn" href="#">Subscribe ›</a>
  </div>
</section>

<section class="services">
  <article class="service">
    <div class="service-photo" role="img" aria-label="Benny performing a balloon show"></div>
    <h3 class="service-title display">Balloon<br>Shows</h3>
    <a class="btn service-btn" href="#">Know More</a>
  </article>
  <article class="service">
    <div class="service-photo" role="img" aria-label="Benny twisting balloon animals"></div>
    <h3 class="service-title display">Balloon<br>Twisting</h3>
    <a class="btn service-btn" href="#">Know More</a>
  </article>
  <article class="service">
    <div class="service-photo" role="img" aria-label="Children at a balloon workshop"></div>
    <h3 class="service-title display">Balloon<br>Workshops</h3>
    <a class="btn service-btn" href="#">Know More</a>
  </article>
  <article class="service">
    <div class="service-photo" role="img" aria-label="Benny with three balloon pigs on his head"></div>
    <h3 class="service-title display">Theater<br>Shows</h3>
    <a class="btn service-btn" href="#">Know More</a>
  </article>
</section>

<footer class="site-footer">
  <div class="footer-top">
    <nav class="footer-nav"><a href="#">Home</a><a href="#">Balloon Shows</a><a href="#">Balloon Twisting</a><a href="#">Theatre</a><a href="#">Booking</a><a href="#">Contact Us</a></nav>
    <div class="social"><span></span><span></span><span></span><span></span><span></span></div>
  </div>
  <div class="copyright">© 2015 Benny The Jester. All Rights Reserved.</div>
</footer>

</body>
</html>
```